WordPress Design for both website and landing page for an expert

I need a clean and stylish design for my new website. I work as an expert (see attached file WHY HOW WHAT), my product is expert opinion (reports) for company evaluations You can use all of the attached pictures colored or black / white. The person is me, you can add other pictures, if you want. The design should be clean and stylish, so you could use white, black, gray, silver and / or one additional color. I have added an idea about my website, see attached file CONCEPT WEBSITE If you have any more information, please do not hesitate to contact us 'Hesitate to ask me ...

```html
<!DOCTYPE html>
<html lang="en">
<head>
<meta charset="UTF-8">
<title>Contact – Elias Marlow</title>
<link href="https://fonts.googleapis.com/css2?family=Montserrat:wght@400;500;600;700&display=swap" rel="stylesheet">
<style>
  :root {
    --bg: #000000;
    --text: #ffffff;
    --text-muted: #c9c9c9;
    --field: #1e1e1e;
    --field-label: #bdbdbd;
    --footer: #1f1f1f;
    --footer-text: #9a9a9a;
    --social: #2e2e2e;
    --photo-top: #2f5f96;
    --photo-bottom: #103452;
    --map-base: #3a3a3a;
    --map-edge: #2a2a2a;
  }
  * { margin: 0; padding: 0; box-sizing: border-box; }
  html, body { width: 1080px; height: 1200px; overflow: hidden; background: var(--bg); }
  body { position: relative; font-family: 'Montserrat', sans-serif; color: var(--text); }

  .site-header .brand {
    position: absolute; left: 32px; top: 48px;
    font-size: 22px; font-weight: 600; letter-spacing: 1px; color: var(--text);
  }
  .site-header .page-title {
    position: absolute; left: 0; width: 1080px; top: 53px; text-align: center;
    font-size: 14px; font-weight: 600; letter-spacing: 1.5px;
  }
  .site-header .close-btn { position: absolute; left: 1008px; top: 51px; width: 20px; height: 20px; }

  .hero { position: absolute; left: 123px; top: 177px; width: 833px; height: 340px; }
  .hero-photo {
    position: absolute; left: 0; top: 0; width: 417px; height: 340px;
    background: linear-gradient(180deg, var(--photo-top) 0%, #3d6a9a 45%, var(--photo-bottom) 100%);
  }
  .hero-map {
    position: absolute; left: 417px; top: 0; width: 416px; height: 340px;
    background: radial-gradient(circle at 55% 50%, var(--map-base), var(--map-edge));
  }
  .hero-title {
    position: absolute; left: 0; width: 833px; top: 104px; text-align: center;
    font-size: 58px; font-weight: 400; letter-spacing: 12px; line-height: 70px;
    padding-left: 12px;
  }

  .contact-info { position: absolute; top: 583px; left: 0; width: 1080px; }
  .info-item { position: absolute; width: 220px; text-align: center; }
  .info-item svg { display: block; margin: 0 auto; }
  .info-item .main { font-size: 15px; margin-top: 16px; color: var(--text-muted); }
  .info-item .sub { font-size: 10px; margin-top: 6px; color: var(--text-muted); }
  .info-item .address { font-size: 11px; line-height: 19px; margin-top: 16px; color: var(--text-muted); }
  .info-phone { left: 229px; }
  .info-address { left: 429px; top: -2px; }
  .info-email { left: 631px; }

  .help-heading {
    position: absolute; top: 738px; left: 0; width: 1080px; text-align: center;
    font-size: 24px; font-weight: 600; line-height: 31px; letter-spacing: 0.5px;
  }

  .contact-form .field {
    position: absolute; background: var(--field); border-radius: 3px;
    font-size: 10px; letter-spacing: 0.8px; color: var(--field-label);
    padding: 13px 0 0 18px; text-transform: uppercase;
  }
  .field-name { left: 255px; top: 833px; width: 200px; height: 36px; }
  .field-email { left: 471px; top: 833px; width: 200px; height: 36px; }
  .field-phone { left: 687px; top: 833px; width: 138px; height: 36px; }
  .field-message { left: 255px; top: 886px; width: 570px; height: 115px; padding-top: 10px !important; }
  .submit-btn {
    position: absolute; left: 475px; top: 1040px; width: 130px; height: 36px;
    border: 1.5px solid var(--text); border-radius: 18px; text-align: center;
    font-size: 11px; font-weight: 600; letter-spacing: 1.2px; line-height: 33px;
  }

  .site-footer {
    position: absolute; left: 0; top: 1138px; width: 1080px; height: 62px; background: var(--footer);
  }
  .site-footer .copyright {
    position: absolute; left: 123px; top: 24px; font-size: 11px; letter-spacing: 0.6px; color: var(--footer-text);
  }
  .social { position: absolute; top: 13px; width: 36px; height: 36px; border-radius: 50%; background: var(--social); }
  .social-1 { left: 826px; }
  .social-2 { left: 873px; }
  .social-3 { left: 920px; }
</style>
</head>
<body>
  <header class="site-header">
    <div class="brand">Marlow</div>
    <div class="page-title">CONTACT</div>
    <svg class="close-btn" viewBox="0 0 20 20" aria-label="Close">
      <path d="M2 2 L18 18 M18 2 L2 18" stroke="#fff" stroke-width="1.8" fill="none"/>
    </svg>
  </header>

  <section class="hero">
    <div class="hero-photo" role="img" aria-label="Evening photo of a riverside city skyline with a tall tower"></div>
    <div class="hero-map" role="img" aria-label="Dark road map of the region"></div>
    <h1 class="hero-title">CONTACT<br>ME</h1>
  </section>

  <section class="contact-info">
    <div class="info-item info-phone">
      <svg width="22" height="22" viewBox="0 0 24 24" aria-hidden="true">
        <path d="M5 3 L8.5 3 L10 7.5 L7.8 9.2 C9 11.8 12.2 15 14.8 16.2 L16.5 14 L21 15.5 L21 19 C21 20 20 21 19 21 C10.5 20.5 3.5 13.5 3 5 C3 4 4 3 5 3 Z" fill="none" stroke="#fff" stroke-width="1.5" stroke-linejoin="round"/>
      </svg>
      <div class="main">+1-410-555-0182</div>
      <div class="sub">Call Us Today!</div>
    </div>
    <div class="info-item info-address">
      <svg width="22" height="28" viewBox="0 0 22 28" aria-hidden="true">
        <path d="M11 26 C11 26 2 15.5 2 10 A9 9 0 0 1 20 10 C20 15.5 11 26 11 26 Z" fill="none" stroke="#fff" stroke-width="1.6"/>
        <circle cx="11" cy="10" r="3" fill="none" stroke="#fff" stroke-width="1.6"/>
      </svg>
      <div class="address">24 Lindenweg Lane<br>Westbrook, MD 20740<br>Germany</div>
    </div>
    <div class="info-item info-email">
      <svg width="24" height="22" viewBox="0 0 24 22" aria-hidden="true">
        <rect x="2" y="5" width="20" height="13" fill="none" stroke="#fff" stroke-width="1.6"/>
        <path d="M2 5 L12 12.5 L22 5" fill="none" stroke="#fff" stroke-width="1.6"/>
      </svg>
      <div class="main">hello@marlowreports.com</div>
      <div class="sub">Inquire Now!</div>
    </div>
  </section>

  <h2 class="help-heading">How can I help<br>you today!</h2>

  <form class="contact-form">
    <div class="field field-name">Enter your name</div>
    <div class="field field-email">Email</div>
    <div class="field field-phone">Phone</div>
    <div class="field field-message">Message</div>
    <div class="submit-btn">SUBMIT</div>
  </form>

  <footer class="site-footer">
    <div class="copyright">Copyright © 2018 Elias Marlow. All Rights Reserved</div>
    <span class="social social-1" aria-label="Social link"></span>
    <span class="social social-2" aria-label="Social link"></span>
    <span class="social social-3" aria-label="Social link"></span>
  </footer>
</body>
</html>
```